4th Generation Family Business Needs a New Card Design!

We are a family owned 4th Generation company. We are based in the Sydney, Australia area and we are desperately in need of a more modern and classy card. We are monumental masons who design, supply & erect lasting memorials throughout cemeteries in Sydney. Our customers are normally in a period of grieving. I have attached logo files that will need to be implemented on the card. Company was established 1935. Australian Owned and Operated. Card needs to be designed to PIXO.com specification.

Target Market(s)

Our target market is based upon people that a grieving for family members that have passed away. We also deal with alot of companies that own and operate cemeteries.

Industry/Entity Type

Business

Contact Information for Business Card

Simon Harcourt, Operations Manager, 0417293086, simon@harcourtmemorials.com.au
Lewis Harcourt, Director, 0491630572, lewis@harcourtmemorials.com.au
Phone # 02 9561 3048
Website: www.harcourtmemorials.com.au
Address: Suite 17, 8 Palfrey Lane, West Carlow, Sydney NSW 2156

Font styles to use
Serif
Decorative
Script

Requirements
Must have
• Would like to see the logo nicely implemented with a modern design. Embossed lettering would be a nice additive.

```html
<!DOCTYPE html>
<html lang="en">
<head>
<meta charset="utf-8">
<title>Harcourt Memorials – Business Card</title>
<link rel="stylesheet" href="https://fonts.googleapis.com/css2?family=Open+Sans:wght@400;600;700&display=swap">
<style>
  :root {
    --stage: #2a2c30;
    --gold: #e9bd2c;
    --gold-deep: #dcae1f;
    --gold-light: #f0c93e;
    --paper: #ffffff;
    --ink: #1d1d1d;
    --ink-soft: #2f2f2f;
  }
  * { box-sizing: border-box; margin: 0; padding: 0; }
  html, body {
    width: 1200px; height: 864px; overflow: hidden;
    background: var(--stage);
    font-family: "Open Sans", Arial, sans-serif;
  }
  .stage { position: relative; width: 1200px; height: 864px; }

  .card {
    position: absolute; left: 330px; width: 540px; height: 330px;
    overflow: hidden;
  }
  .card--front { top: 86px; }
  .card--back { top: 446px; background: var(--paper); color: var(--ink-soft); }

  /* front */
  .emboss-field {
    position: absolute; inset: 0;
    background: radial-gradient(ellipse at 50% 45%, var(--gold-light) 0%, var(--gold) 55%, var(--gold-deep) 100%);
  }
  .front-wordmark {
    position: absolute; left: 0; right: 0; top: 128px;
    text-align: center; color: var(--paper);
    font-weight: 600; font-size: 34px; letter-spacing: 3px; line-height: 1.15;
    text-transform: uppercase;
  }
  .front-wordmark small { display: block; font-size: 17px; letter-spacing: 6px; }

  /* back */
  .divider {
    position: absolute; left: 0; right: 0; top: 166px;
    height: 1.5px; background: var(--gold);
  }
  .contact { position: absolute; font-size: 12.5px; line-height: 17px; }
  .contact .name { color: var(--gold); font-weight: 700; font-size: 15.5px; line-height: 20px; }
  .contact .row { display: flex; align-items: center; gap: 6px; }
  .contact--left { left: 30px; top: 34px; }
  .contact--right { right: 30px; top: 222px; text-align: right; }
  .contact--right .row { justify-content: flex-end; }
  .icon { width: 10px; height: 10px; flex: none; }

  .office { position: absolute; left: 30px; top: 182px; font-size: 12.5px; line-height: 17px; }
  .office .label, .office .web { color: var(--gold); }
  .office .label span { color: var(--ink-soft); }

  .back-wordmark {
    position: absolute; right: 34px; top: 62px; width: 220px;
    text-align: center; color: var(--ink);
    font-weight: 600; font-size: 27px; letter-spacing: 2px; line-height: 1.15;
    text-transform: uppercase;
  }
  .back-wordmark small { display: block; font-size: 14px; letter-spacing: 5px; }
</style>
</head>
<body>
<main class="stage">

  <section class="card card--front" aria-label="Card front">
    <div class="emboss-field" role="img" aria-label="Embossed repeating monument pattern on gold card stock"></div>
    <div class="front-wordmark">Harcourt<small>Memorials</small></div>
  </section>

  <section class="card card--back" aria-label="Card back">
    <div class="contact contact--left">
      <p class="name">Simon Harcourt</p>
      <p>Operations Manager</p>
      <p class="row">
        <svg class="icon" viewBox="0 0 10 10"><path fill="var(--gold)" d="M2 0.5l1.6 2-1 1.1c.6 1.3 1.5 2.2 2.8 2.8l1.1-1 2 1.6-.9 1.6C4.6 8.4 1.6 5.4 0.4 1.4z"/></svg>
        0417293086
      </p>
      <p class="row">
        <svg class="icon" viewBox="0 0 10 10"><rect x="0.5" y="2" width="9" height="6.5" fill="var(--gold)"/><path d="M0.8 2.3L5 5.6l4.2-3.3" stroke="#fff" stroke-width="0.9" fill="none"/></svg>
        simon@harcourtmemorials.com.au
      </p>
    </div>

    <div class="back-wordmark">Harcourt<small>Memorials</small></div>

    <div class="divider"></div>

    <div class="office">
      <p class="label">P: <span>02 9561 3048</span></p>
      <p class="web">www.harcourtmemorials.com.au</p>
      <p>Suite 17, 8 Palfrey Lane, West Carlow,</p>
      <p>Sydney NSW 2156</p>
    </div>

    <div class="contact contact--right">
      <p class="name">Lewis Harcourt</p>
      <p>Director</p>
      <p class="row">
        0491630572
        <svg class="icon" viewBox="0 0 10 10"><path fill="var(--gold)" d="M2 0.5l1.6 2-1 1.1c.6 1.3 1.5 2.2 2.8 2.8l1.1-1 2 1.6-.9 1.6C4.6 8.4 1.6 5.4 0.4 1.4z"/></svg>
      </p>
      <p class="row">
        lewis@harcourtmemorials.com.au
        <svg class="icon" viewBox="0 0 10 10"><rect x="0.5" y="2" width="9" height="6.5" fill="var(--gold)"/><path d="M0.8 2.3L5 5.6l4.2-3.3" stroke="#fff" stroke-width="0.9" fill="none"/></svg>
      </p>
    </div>
  </section>

</main>
</body>
</html>
```